Food Hall in San Clemente, CA by the Pacific Ocean that has 15 vendors and 2 bars

We need a web page design that highlights our food hall in San Clemente, CA. The name of the food hall is Calloway Food Hall. Inside of the food hall there are 15 different vendors and 2 bars. The place has a beautiful patio and it is by Pacific Ocean. Most of the vendors are local to San Clemente area. The highly anticipated location is opening during the summer of 2025. Website should have a dropdown menu for the different vendors that are in the food hall and people should be able to click to their respective business website. The website should also include link to our social media channels and also a link to provide comments and subscribe for the mailing list.
Target Market(s)
Mostly residents in the San Clemente, CA and surrounding areas. Couples, families and tourist alike that are looking for an exceptional dining experience that everyone can find something they like.
Industry/Entity Type
Restaurants
Coding
Number of Pages Required
Font styles to use
Look and feel

```html
<!DOCTYPE html>
<html lang="en">
<head>
<meta charset="UTF-8">
<title>Calloway Food Hall – San Clemente</title>
<link href="https://fonts.googleapis.com/css2?family=Oswald:wght@500;600&family=Roboto:wght@400;500;700&display=swap" rel="stylesheet">
<style>
:root{
  --navy:#0b3f99;
  --blue:#0d5cc0;
  --sky:#1a93db;
  --pale:#eef6fb;
  --ink:#1d2330;
  --text:#555b66;
  --line:#c9d3de;
  --white:#ffffff;
}
*{margin:0;padding:0;box-sizing:border-box}
html,body{width:1200px;height:4930px;overflow:hidden}
body{position:relative;font-family:"Roboto",Arial,sans-serif;color:var(--text);background:var(--white)}
.abs{position:absolute}
.heading{font-family:"Oswald","Arial Narrow",sans-serif;font-weight:600;text-transform:uppercase;letter-spacing:-.5px;line-height:1.15}
.heading .accent{color:var(--sky)}
.btn{position:absolute;display:flex;align-items:center;justify-content:center;gap:8px;height:48px;border-radius:26px;font-size:12px;font-weight:700;text-transform:uppercase;color:var(--white);background:linear-gradient(90deg,var(--navy),var(--sky));text-decoration:none}
.btn .arrow{width:14px;height:14px;border-radius:50%;background:var(--white);display:inline-flex;align-items:center;justify-content:center}
.btn .arrow svg{width:8px;height:8px}
.btn.light{background:var(--white);color:var(--navy);border:2px solid var(--white)}
.btn.light .arrow{background:var(--navy)}

/* top bar */
.topbar{left:0;top:0;width:1200px;height:44px}
.topbar .info{position:absolute;top:11px;font-size:13px;font-weight:500;color:var(--white)}
.brand{position:absolute;left:0;width:1200px;top:10px;text-align:center;font-family:"Oswald",sans-serif;font-weight:600;font-size:33px;color:var(--sky)}

/* hero */
.hero{left:0;top:0;width:1200px;height:690px;background:linear-gradient(180deg,#8ac6ea 0%,#c8e6f7 38%,#5c98c4 48%,#2f6fa3 62%,#4b7a4f 78%,#2c5b35 100%)}
.nav{position:absolute;top:96px;left:0;width:1200px;display:flex;justify-content:center;gap:0;font-size:13px;font-weight:500;color:var(--ink)}
.nav a{color:var(--ink);text-decoration:none;padding:0 21px;border-left:1px solid #596274;line-height:14px}
.nav a:first-child{border-left:0;border-bottom:3px solid var(--sky);padding-bottom:5px}
.hero h1{position:absolute;top:182px;width:1200px;text-align:center;font-size:52px;color:var(--white);line-height:1.2;text-shadow:0 2px 6px rgba(0,50,110,.45)}
.hero .sub{position:absolute;top:340px;width:1200px;text-align:center;font-size:16px;color:var(--white);text-shadow:0 1px 4px rgba(0,0,0,.5)}
.dots{left:1106px;top:422px}
.dots span{display:block;width:9px;height:9px;border-radius:50%;background:var(--white);margin-bottom:9px}
.dots span.on{background:transparent;border:2px solid var(--white)}

/* welcome */
.welcome-title{left:145px;top:716px;font-size:50px;color:var(--navy)}
.welcome-text{left:145px;top:860px;width:428px;font-size:14px;line-height:27.3px;text-align:justify}
.welcome-photo{left:632px;top:727px;width:424px;height:350px;background:linear-gradient(160deg,#6b8fab 0%,#3b7ea8 30%,#e4d6b8 48%,#58724d 62%,#8a7464 100%)}
.welcome-frame{left:903px;top:955px;width:205px;height:194px;border:3px solid var(--sky);border-radius:6px}
.play{left:878px;top:1048px;width:46px;height:46px;border-radius:50%;background:var(--white);display:flex;align-items:center;justify-content:center}
.play span{width:34px;height:34px;border-radius:50%;background:var(--sky);display:flex;align-items:center;justify-content:center}
.dotgrid{background-image:radial-gradient(circle,#4a6f9c 1.6px,transparent 1.8px);background-size:11px 11px}

/* why */
.why{left:0;top:1244px;width:1200px;height:642px;background:var(--pale)}
.section-title{position:absolute;left:0;width:1200px;text-align:center;font-size:47px;color:var(--navy)}
.feature{position:absolute;top:240px;width:266px;height:305px;background:var(--white);border:1px solid var(--line);text-align:center}
.feature.active{border:3px solid var(--sky)}
.feature .diamond{position:absolute;left:50%;top:-50px;width:72px;height:72px;margin-left:-36px;background:var(--navy);transform:rotate(45deg);display:flex;align-items:center;justify-content:center}
.feature.active .diamond{background:var(--sky)}
.feature .diamond i{display:block;width:28px;height:28px;border:3px solid var(--white);border-radius:6px;transform:rotate(-45deg)}
.feature h3{margin-top:60px;font-size:15px;font-weight:500;color:var(--ink);line-height:23px;text-transform:uppercase}
.feature p{margin:16px auto 0;width:200px;font-size:12.5px;line-height:23px}
.feature .btn{left:50%;margin-left:-71px;width:142px;height:42px;top:232px}
.corner{position:absolute;border-color:var(--sky);border-style:solid;width:70px;height:64px}

/* countdown */
.count{left:0;top:1886px;width:1200px;height:338px;background:linear-gradient(90deg,#0b3e95 0%,#0f5cb8 55%,#1c8fd8 100%)}
.count .skyline{position:absolute;left:60px;bottom:0;width:1080px;height:120px;background:linear-gradient(180deg,rgba(255,255,255,0) 0%,rgba(120,170,220,.18) 100%)}
.count h2{position:absolute;top:68px;width:1200px;text-align:center;font-size:47px;color:var(--white)}
.unit{position:absolute;top:164px;width:76px;height:97px;border:1px solid rgba(255,255,255,.55);border-radius:4px;text-align:center;color:var(--white);font-family:"Oswald",sans-serif}
.unit b{display:block;font-size:40px;font-weight:500;line-height:58px}
.unit small{font-size:19px;font-weight:500}
.sep{position:absolute;top:205px;color:var(--white);font-size:22px;font-weight:700}

/* vendors */
.vendor{position:absolute;top:2440px;width:275px;height:447px;background:var(--white);border:1px solid var(--line);text-align:center}
.vendor.raised{box-shadow:0 4px 18px rgba(0,40,90,.15)}
.vendor .ring{position:absolute;left:50%;top:14px;width:207px;height:207px;margin-left:-103px;border:2px solid #6cb4e0;border-radius:50%;padding:7px}
.vendor .ring div{width:100%;height:100%;border-radius:50%}
.vendor .badge{position:absolute;left:50%;top:192px;width:38px;height:38px;margin-left:-19px;border-radius:50%;background:var(--navy);border:3px solid var(--white)}
.vendor .badge::after{content:"";position:absolute;left:10px;top:10px;width:12px;height:12px;border:2px solid var(--white);border-radius:4px}
.vendor h3{position:absolute;top:252px;width:100%;font-size:16px;font-weight:500;color:var(--ink);text-transform:uppercase}
.vendor p{position:absolute;top:282px;left:50%;width:200px;margin-left:-100px;font-size:13px;line-height:23px}
.tags{position:absolute;top:376px;width:100%;display:flex;justify-content:center;gap:7px}
.tags span{font-size:10px;color:var(--blue);background:#e1eff9;padding:3px 11px;border-radius:10px}
.vendor .btn{left:50%;margin-left:-71px;width:142px;height:42px;top:424px}
.slide-arrow{position:absolute;top:2643px;width:42px;height:42px;border-radius:50%;border:1px solid #3a4150;background:var(--white);display:flex;align-items:center;justify-content:center}

/* mailing */
.mailing{left:0;top:2997px;width:1200px;height:343px;background:linear-gradient(90deg,#0c4a9e 0%,#1567b8 45%,#2a85c8 75%,#16509e 100%)}
.mailing h2{position:absolute;top:88px;width:1200px;text-align:center;font-size:50px;color:var(--white)}
.mailing .field{position:absolute;left:351px;top:195px;width:346px;height:46px;border-radius:24px;background:var(--white);font-size:13px;color:var(--ink);padding:15px 36px}
.mailing .btn{left:704px;top:195px;width:144px;height:46px;border:2px solid var(--white)}

/* gallery */
.tile{position:absolute;height:297px}

/* reserve */
.lower{left:0;top:4100px;width:1200px;height:830px;background:linear-gradient(180deg,#ffffff 0%,#dcecf7 20%,#a9d0ec 45%,#6aa7d2 60%,#0b3f99 62%,#0a3a90 100%)}
.card{left:132px;top:4291px;width:936px;height:437px;background:var(--white)}
.card h2{position:absolute;top:50px;font-size:35px;color:var(--navy)}
.input{position:absolute;left:27px;width:264px;height:34px;border:1px solid #8c939d;font-size:11px;color:var(--ink);padding:10px 20px}
.card .btn{left:27px;top:355px;width:264px;height:36px;border-radius:18px;font-size:11px}
.card .photo{position:absolute;left:312px;top:25px;width:312px;height:383px;background:radial-gradient(circle at 50% 55%,#d98a52 0%,#b95b33 30%,#3a2b24 60%,#1f1a18 100%)}
.contact-row{position:absolute;left:674px;display:flex;align-items:center;gap:14px;font-size:12px;color:var(--ink);line-height:22px}
.contact-row .ic{flex:none;width:46px;height:46px;border-radius:50%;border:1px solid var(--line);display:flex;align-items:center;justify-content:center;background:var(--white)}
.contact-row .ic.on{background:var(--navy);border-color:var(--navy)}
.contact-row svg{width:16px;height:16px}

/* footer */
.socials{left:0;top:4789px;width:1200px;display:flex;justify-content:center;gap:11px}
.socials span{width:37px;height:37px;border-radius:50%;border:2px solid var(--white);display:block}
.copyright{left:0;top:4862px;width:1200px;text-align:center;font-size:12px;color:var(--white)}
</style>
</head>
<body>

<!-- hero -->
<section class="abs hero" role="img" aria-label="Coastal view of the Pacific Ocean with green shrubs on the bluff under a bright sky">
  <svg class="abs" style="left:0;top:0" width="1200" height="44" viewBox="0 0 1200 44" aria-hidden="true">
    <polygon points="0,0 490,0 470,40 0,40" fill="#0d5cc0"/>
    <polygon points="710,0 1200,0 1200,40 730,40" fill="#1a8fd8"/>
    <polygon points="490,0 710,0 730,40 470,40" fill="#ffffff"/>
  </svg>
  <div class="info" style="position:absolute;left:145px;top:11px;font-size:13px;font-weight:500;color:#fff">✉ Email : hello@callowayhall.com</div>
  <div class="info" style="position:absolute;left:862px;top:11px;font-size:13px;font-weight:500;color:#fff">✆ Phone : +1 555 014 2290</div>
  <div class="brand">Calloway Food Hall</div>

  <nav class="nav">
    <a href="#">HOME</a><a href="#">ABOUT US</a><a href="#">SERVICES</a><a href="#">NEWS</a><a href="#">GALLERY</a><a href="#">EVENTS</a><a href="#">CONTACT US</a>
  </nav>

  <h1 class="heading">15 Local Flavors. 2 Bars.<br>1 Iconic Spot by the Ocean</h1>
  <p class="sub">A new coastal culinary destination in the heart of San Clemente.</p>
  <a class="btn" href="#" style="left:374px;top:385px;width:206px">Meet the Vendors <span class="arrow"><svg viewBox="0 0 8 8"><path d="M2 1l3 3-3 3" stroke="#0b3f99" stroke-width="1.6" fill="none"/></svg></span></a>
  <a class="btn light" href="#" style="left:592px;top:385px;width:234px">Join Our Mailing List <span class="arrow"><svg viewBox="0 0 8 8"><path d="M2 1l3 3-3 3" stroke="#fff" stroke-width="1.6" fill="none"/></svg></span></a>
  <div class="abs dots"><span></span><span class="on"></span><span class="on"></span></div>

  <svg class="abs" style="left:0;top:500px" width="1200" height="190" viewBox="0 0 1200 190" preserveAspectRatio="none" aria-hidden="true">
    <path d="M0 170 L600 65 L1200 165 L1200 190 L0 190Z" fill="#ffffff"/>
    <path d="M0 160 L600 55 L1200 158" stroke="#0b3f99" stroke-width="7" fill="none"/>
    <path d="M0 150 L600 45 L1200 150" stroke="#1a8fd8" stroke-width="3" fill="none"/>
  </svg>
</section>

<!-- welcome -->
<h2 class="abs heading welcome-title">Welcome to<br><span class="accent">Calloway Food Hall</span></h2>
<p class="abs welcome-text">Sed ut perspiciatis unde omnis iste natus error sit voluptatem accusantium doloremque laudantium, totam rem aperiam, eaque ipsa quae ab illo inventore veritatis et quasi architecto beatae vitae dicta sunt explicabo. Nemo enim ipsam voluptatem quia voluptas sit aspernatur aut odit aut fugit, sed quia consequuntur magni dolores eos qui ratione voluptatem sequi nesciporro quisquam est, qui dolorem ipsum quia dolor sit amet, consectetur, adipiscdi tempora incidunt</p>
<a class="btn" href="#" style="left:145px;top:1107px;width:160px;height:50px">Read More <span class="arrow"><svg viewBox="0 0 8 8"><path d="M2 1l3 3-3 3" stroke="#0b3f99" stroke-width="1.6" fill="none"/></svg></span></a>
<div class="abs welcome-frame"></div>
<div class="abs dotgrid" style="left:1060px;top:985px;width:42px;height:120px"></div>
<div class="abs dotgrid" style="left:962px;top:1080px;width:120px;height:22px"></div>
<div class="abs welcome-photo" role="img" aria-label="Aerial view of the San Clemente coastline with beach, bluffs and hillside homes"></div>
<div class="abs play"><span><svg width="12" height="14" viewBox="0 0 12 14"><path d="M1 1l10 6-10 6z" fill="#fff"/></svg></span></div>

<!-- why choose -->
<section class="abs why">
  <h2 class="section-title heading" style="top:72px">Why Choose <span class="accent">Calloway Food Hall</span></h2>
  <div class="corner" style="left:145px;top:230px;border-width:3px 0 0 3px"></div>
  <div class="corner" style="left:990px;top:493px;border-width:0 3px 3px 0"></div>
  <div class="abs dotgrid" style="left:448px;top:245px;width:20px;height:100px"></div>
  <div class="abs dotgrid" style="left:660px;top:455px;width:100px;height:100px;background-size:11px 11px;clip-path:polygon(80% 0,100% 0,100% 100%,0 100%,0 80%,80% 80%)"></div>

  <div class="feature" style="left:157px">
    <div class="diamond"><i></i></div>
    <h3>Local Vendors<br>Local Love</h3>
    <p>Sed ut perspiciatis unde omnis iste natus error sit voluptatem accusantium doloremqueantium, totam rem aperiam</p>
    <a class="btn" href="#">Read More <span class="arrow"><svg viewBox="0 0 8 8"><path d="M2 1l3 3-3 3" stroke="#0b3f99" stroke-width="1.6" fill="none"/></svg></span></a>
  </div>
  <div class="feature active" style="left:467px;top:244px;width:274px">
    <div class="diamond"><i></i></div>
    <h3>Coastal Patio<br>Vibes</h3>
    <p>Sed ut perspiciatis unde omnis iste natus error sit voluptatem accusantium doloremqueantium, totam rem aperiam</p>
    <a class="btn" href="#" style="top:228px">Read More <span class="arrow"><svg viewBox="0 0 8 8"><path d="M2 1l3 3-3 3" stroke="#0b3f99" stroke-width="1.6" fill="none"/></svg></span></a>
  </div>
  <div class="feature" style="left:781px">
    <div class="diamond"><i></i></div>
    <h3>Something for<br>Everyone</h3>
    <p>Sed ut perspiciatis unde omnis iste natus error sit voluptatem accusantium doloremqueantium, totam rem aperiam</p>
    <a class="btn" href="#">Read More <span class="arrow"><svg viewBox="0 0 8 8"><path d="M2 1l3 3-3 3" stroke="#0b3f99" stroke-width="1.6" fill="none"/></svg></span></a>
  </div>
</section>

<!-- countdown -->
<section class="abs count">
  <div class="skyline" role="img" aria-label="Faint view of the San Clemente pier and palm trees"></div>
  <h2 class="heading">Opening Summer 2025</h2>
  <div class="unit" style="left:387px"><b>02</b><small>Days</small></div>
  <span class="sep" style="left:481px">:</span>
  <div class="unit" style="left:503px"><b>03</b><small>Hours</small></div>
  <span class="sep" style="left:597px">:</span>
  <div class="unit" style="left:619px"><b>30</b><small>Mins</small></div>
  <span class="sep" style="left:713px">:</span>
  <div class="unit" style="left:735px"><b>20</b><small>Secs</small></div>
</section>

<!-- featured vendors -->
<h2 class="section-title heading" style="top:2318px">Featured <span class="accent">Vendors</span></h2>
<div class="slide-arrow" style="left:72px"><svg width="12" height="16" viewBox="0 0 12 16"><path d="M9 2L3 8l6 6" stroke="#1d2330" stroke-width="2" fill="none"/></svg></div>
<div class="slide-arrow" style="left:1084px"><svg width="12" height="16" viewBox="0 0 12 16"><path d="M3 2l6 6-6 6" stroke="#1d2330" stroke-width="2" fill="none"/></svg></div>

<div class="vendor" style="left:144px">
  <div class="ring"><div role="img" aria-label="Lively food hall interior with bright signage" style="background:radial-gradient(circle at 50% 40%,#d9a25a 0%,#6a4a3a 45%,#2a3a4a 100%)"></div></div>
  <span class="badge"></span>
  <h3>Sit Voluptatem</h3>
  <p>Sed ut perspiciatis unde omnis iste natus error sit voluptatem accusan</p>
  <div class="tags"><span>Pizza</span><span>Tacos</span><span>Vegan</span><span>Dessert</span></div>
  <a class="btn" href="#">Read More <span class="arrow"><svg viewBox="0 0 8 8"><path d="M2 1l3 3-3 3" stroke="#0b3f99" stroke-width="1.6" fill="none"/></svg></span></a>
</div>
<div class="vendor raised" style="left:463px">
  <div class="ring"><div role="img" aria-label="Food hall building front at dusk" style="background:linear-gradient(180deg,#5b6fa8 0%,#8a7da8 40%,#c58a4a 65%,#3a2e2a 100%)"></div></div>
  <span class="badge"></span>
  <h3>Accusantium</h3>
  <p>Sed ut perspiciatis unde omnis iste natus error sit voluptatem accusan</p>
  <div class="tags"><span>Pizza</span><span>Tacos</span><span>Vegan</span><span>Dessert</span></div>
  <a class="btn" href="#">Read More <span class="arrow"><svg viewBox="0 0 8 8"><path d="M2 1l3 3-3 3" stroke="#0b3f99" stroke-width="1.6" fill="none"/></svg></span></a>
</div>
<div class="vendor" style="left:782px">
  <div class="ring"><div role="img" aria-label="White coastal building with red tile roof and palm trees" style="background:linear-gradient(180deg,#cfe4f3 0%,#e8ecee 45%,#b86a4e 60%,#6f8b5a 100%)"></div></div>
  <span class="badge"></span>
  <h3>Uptatcusantium</h3>
  <p>Sed ut perspiciatis unde omnis iste natus error sit voluptatem accusan</p>
  <div class="tags"><span>Pizza</span><span>Tacos</span><span>Vegan</span><span>Dessert</span></div>
  <a class="btn" href="#">Read More <span class="arrow"><svg viewBox="0 0 8 8"><path d="M2 1l3 3-3 3" stroke="#0b3f99" stroke-width="1.6" fill="none"/></svg></span></a>
</div>

<!-- mailing list -->
<section class="abs mailing" role="img" aria-label="Blue tinted scene of people sharing food at a table">
  <h2 class="heading">Join Our Mailing List</h2>
  <div class="field">Enter EMail</div>
  <a class="btn" href="#">Sign Up <span class="arrow"><svg viewBox="0 0 8 8"><path d="M2 1l3 3-3 3" stroke="#0b3f99" stroke-width="1.6" fill="none"/></svg></span></a>
</section>

<!-- lower background -->
<div class="abs lower" role="img" aria-label="Coastal bluff and ocean horizon fading into a deep blue band"></div>
<svg class="abs" style="left:0;top:4440px" width="1200" height="90" viewBox="0 0 1200 90" preserveAspectRatio="none" aria-hidden="true">
  <path d="M0 30 L600 70 L1200 30 L1200 90 L0 90Z" fill="#0b3f99"/>
  <path d="M0 22 L600 62 L1200 22" stroke="#ffffff" stroke-width="4" fill="none"/>
</svg>

<!-- gallery -->
<h2 class="section-title heading" style="top:3430px;color:var(--navy)">Our <span class="accent">Gallery</span></h2>
<div class="tile" style="left:144px;top:3537px;width:297px;background:linear-gradient(135deg,#8a3a5a,#c24a4a 40%,#d9d07a 65%,#3a6a3a)" role="img" aria-label="Sliced tuna wraps with greens and purple cabbage"></div>
<div class="tile" style="left:452px;top:3537px;width:297px;background:linear-gradient(135deg,#e6c98a,#d9a25a 45%,#7aa05a 70%,#e8d4b0)" role="img" aria-label="Hands holding cut wraps filled with vegetables"></div>
<div class="tile" style="left:760px;top:3537px;width:296px;background:linear-gradient(135deg,#d4dde4,#a9b6c0 40%,#c96a3a 60%,#3e5a3a)" role="img" aria-label="Fresh salad with crispy tortilla strips"></div>
<div class="tile" style="left:144px;top:3845px;width:297px;background:linear-gradient(160deg,#2a1e18,#8a5a2a 45%,#d98a3a 70%,#3a1a10)" role="img" aria-label="Grilled skewers over a flaming barbecue"></div>
<div class="tile" style="left:452px;top:3845px;width:604px;background:linear-gradient(135deg,#1e3a6a,#2f5c96 45%,#5a7ab0 70%,#1e3468)" role="img" aria-label="Table of shared plates seen from above with a blue tint"></div>
<div class="abs" style="left:734px;top:3974px;width:40px;height:40px;border-radius:50%;background:var(--sky);color:#fff;font-size:22px;line-height:38px;text-align:center">+</div>
<a class="btn" href="#" style="left:530px;top:4178px;width:142px;height:42px">Load More <span class="arrow"><svg viewBox="0 0 8 8"><path d="M2 1l3 3-3 3" stroke="#0b3f99" stroke-width="1.6" fill="none"/></svg></span></a>

<!-- reserve & contact -->
<section class="abs card">
  <h2 class="heading" style="left:27px">Reserve a Table</h2>
  <div class="input" style="top:115px">Enter Name</div>
  <div class="input" style="top:163px">Enter Phone</div>
  <div class="input" style="top:211px">Enter Email</div>
  <div class="input" style="top:259px;height:68px">Message</div>
  <a class="btn" href="#">Submit Message</a>

  <div class="photo" role="img" aria-label="Bowl of shredded salad with tortilla chips"></div>

  <h2 class="heading" style="left:676px">Contact Us</h2>
  <div class="contact-row" style="top:112px"><span class="ic"><svg viewBox="0 0 16 16"><path d="M4 1l2.5 3.5-1.5 1.5c1 2 3 4 5 5l1.5-1.5L15 12l-2 3C7 14 2 9 1 3z" fill="#0b3f99"/></svg></span>Phone: +1 555 014 2290</div>
  <div class="contact-row" style="top:167px"><span class="ic on"><svg viewBox="0 0 16 16"><rect x="1" y="3" width="14" height="10" rx="1" fill="#fff"/><path d="M1 4l7 5 7-5" stroke="#0b3f99" stroke-width="1.4" fill="none"/></svg></span>hello@callowayhall.com</div>
  <div class="contact-row" style="top:222px"><span class="ic"><svg viewBox="0 0 16 16"><circle cx="8" cy="8" r="6.5" stroke="#0b3f99" stroke-width="1.6" fill="none"/><path d="M8 4v4l3 2" stroke="#0b3f99" stroke-width="1.6" fill="none"/></svg></span><span>Mon - Sat &nbsp;&nbsp;&nbsp;18:00 - 23:00<br>Sunday &nbsp;&nbsp;&nbsp;&nbsp;&nbsp;&nbsp;&nbsp;Closed</span></div>
  <div class="contact-row" style="top:285px"><span class="ic"><svg viewBox="0 0 16 16"><path d="M1 3l4.5-1.5 5 1.5L15 1.5v11.5l-4.5 1.5-5-1.5L1 14.5z" fill="#0b3f99"/></svg></span><span>410 Harbor View Lane,<br>San Clemente, California<br>92672</span></div>
</section>

<!-- footer -->
<div class="abs socials" aria-label="Social media links"><span></span><span></span><span></span><span></span><span></span></div>
<p class="abs copyright">© 2025 Calloway Food Hall.All Rights Reserved &nbsp;| &nbsp;Privacy Policy &nbsp;| &nbsp;Terms of use</p>

</body>
</html>
```